App Design - Career Prep Pal

We require an App Design for our new App called 'Hiring Helper'. This app is essentially an assistant to help Users prepare for job interviews, to help them get hired. <br/><br/>Users who download the App can view common Questions and Answers, save their favourite responses and also view common Interview Tips. <br/><br/>The vision for our App is for Users who are preparing for an interview (1 week before, 1 day before, even 1 hour before), are able to download, view and educate themselves on common questions and responses, and then be confident to land the job. <br/><br/>Our team has developed wireframes to help highlight what each screen should do and include. Please see attached document, which also highlights key requirements for the experience. Feel free to add/remove/edit what you see on these wireframes. Our preference is that you use Adobe XD please.<br/><br/>In terms of design guidelines, we want the experience to be simple, intuitive and 'memorable' to help Users to remember the questions/responses when they are in the interview. <br/><br/>The final design should communicate 'neat and clean professionalism'; we like the design of: jobvista net au<br/><br/>Thank you for reading! Good luck !

Target Market(s)

Professional job seekers

Font styles to use
Sans Serif

Colors

Designer to choose colors to be used in the design.

Requirements
Must have
• Please see my PixelGuild_UX file that I have uploaded
Nice to have
• Could you also please include some ideas on how we can incorporate Advertising into the app screens

```html
<!DOCTYPE html>
<html lang="en">
<head>
<meta charset="utf-8">
<title>Hiring Helper – App Screens</title>
<link href="https://fonts.googleapis.com/css2?family=Montserrat:wght@600&family=Open+Sans:wght@400;600&display=swap" rel="stylesheet">
<style>
:root{
  --canvas:#f3f4fa;
  --screen:#ffffff;
  --blue:#2f6bf0;
  --blue-deep:#2a4fb8;
  --blue-light:#4d8dff;
  --ink:#3c3f46;
  --muted:#9aa0ad;
  --nav-bg:#f6f7f9;
  --nav-icon:#c4c7ce;
  --nav-active:#23262d;
  --tick:#2bbf4a;
  --card-shadow:rgba(70,90,160,.14);
}
*{box-sizing:border-box;margin:0;padding:0}
html,body{width:1200px;height:686px;overflow:hidden}
body{background:var(--canvas);font-family:"Open Sans",Arial,sans-serif;color:var(--ink);position:relative}
.screen{position:absolute;top:43px;width:277px;height:602px;background:var(--screen);border-radius:28px;overflow:hidden;box-shadow:0 14px 40px rgba(90,100,200,.18)}
.screen--welcome{left:92px}
.screen--menu{left:445px}
.screen--categories{left:799px}
.header{position:absolute;left:0;top:0;width:100%;height:170px;background:linear-gradient(160deg,var(--blue-deep) 0%,var(--blue) 60%,var(--blue-light) 100%)}
.status{position:absolute;top:12px;left:0;width:100%;display:flex;justify-content:space-between;padding:0 18px 0 26px;color:#fff;font-size:10.5px;font-weight:600}
.status svg{display:block}
.brand{position:absolute;left:0;width:100%;text-align:center;color:#fff;font-family:"Montserrat",Arial,sans-serif;font-weight:600;font-size:18px;letter-spacing:.2px}
.sheet{position:absolute;left:0;width:100%;bottom:0;background:var(--screen);border-radius:16px 16px 0 0}
.intro-card{position:absolute;left:0;top:126px;width:100%;height:229px;background:#fff;border-radius:14px 14px 12px 12px;box-shadow:0 6px 14px var(--card-shadow);text-align:center}
.intro-card svg{position:absolute;left:123px;top:35px}
.intro-card p{position:absolute;left:12px;right:12px;top:86px;font-size:11.6px;line-height:22px}
.option{position:absolute;height:50px;background:#fff;box-shadow:0 2px 10px var(--card-shadow);border-left:6px solid var(--blue);border-radius:3px;display:flex;align-items:center;justify-content:center;font-size:13px}
.screen--menu .option{left:13px;width:255px}
.screen--categories .option{left:15px;width:253px}
.illustration{position:absolute;left:76px;top:406px;width:108px;height:88px;border-radius:14px;background:linear-gradient(140deg,#cfe0ff 0%,#5b8cf5 55%,#f7c6cf 100%);opacity:.85}
.section-title{position:absolute;left:0;width:100%;top:158px;text-align:center;color:var(--blue);font-weight:600;font-size:15px}
.section-sub{position:absolute;left:0;width:100%;top:190px;text-align:center;font-size:12.5px}
.btn-view-all{position:absolute;left:90px;top:508px;width:97px;height:32px;background:var(--blue);color:#fff;border-radius:3px;font-size:12.5px;display:flex;align-items:center;justify-content:center}
.nav{position:absolute;left:0;bottom:0;width:100%;height:40px;background:var(--nav-bg);display:flex;justify-content:space-around;align-items:center;padding:0 14px}
.nav svg{display:block}
</style>
</head>
<body>

<!-- Welcome screen -->
<section class="screen screen--welcome">
  <div class="header" role="img" aria-label="Blue-tinted photo of an interview meeting"></div>
  <div class="status"><span>9:30</span>
    <svg width="44" height="10" viewBox="0 0 44 10" fill="#fff"><rect x="0" y="6" width="2" height="4"/><rect x="3" y="4" width="2" height="6"/><rect x="6" y="2" width="2" height="8"/><rect x="9" y="0" width="2" height="10"/><path d="M16 4a7 7 0 0 1 10 0l-1 1a5.5 5.5 0 0 0-8 0z M18 6a4 4 0 0 1 6 0l-3 3z"/><rect x="30" y="1" width="12" height="8" rx="1.5" fill="none" stroke="#fff"/><rect x="31.5" y="2.5" width="9" height="5"/><rect x="42.5" y="3.5" width="1.2" height="3"/></svg>
  </div>
  <div class="brand" style="top:49px">Hiring Helper</div>
  <div class="intro-card">
    <svg width="30" height="30" viewBox="0 0 30 30" fill="none" stroke="var(--tick)" stroke-width="2.4" stroke-linecap="round" stroke-linejoin="round"><path d="M26 13.5A12 12 0 1 1 19 4"/><path d="M9 14l5 5L28 4"/></svg>
    <p>Your Guide to the Most Common Interview Qustions, and the best Resonsws to help you Get hired.</p>
  </div>
  <nav class="nav">
    <svg width="16" height="16" viewBox="0 0 16 16" fill="var(--nav-active)"><path d="M8 1L1 7.5h2V15h4v-4h2v4h4V7.5h2z"/></svg>
    <svg width="16" height="16" viewBox="0 0 16 16" fill="none" stroke="var(--nav-icon)" stroke-width="2"><circle cx="7" cy="7" r="5"/><path d="M11 11l4 4"/></svg>
    <svg width="18" height="18" viewBox="0 0 18 18"><rect width="18" height="18" rx="4" fill="var(--nav-icon)"/><path d="M9 5v8M5 9h8" stroke="#fff" stroke-width="2"/></svg>
    <svg width="17" height="15" viewBox="0 0 17 15" fill="var(--nav-icon)"><path d="M8.5 15L1.5 8A4 4 0 0 1 8.5 2.5 4 4 0 0 1 15.5 8z"/></svg>
    <svg width="16" height="16" viewBox="0 0 16 16" fill="var(--nav-icon)"><circle cx="8" cy="5" r="4"/><path d="M0 16c0-5 3.5-6.5 8-6.5s8 1.5 8 6.5z"/></svg>
  </nav>
</section>

<!-- Main menu screen -->
<section class="screen screen--menu">
  <div class="header" role="img" aria-label="Blue-tinted photo of an interview meeting"></div>
  <div class="status"><span>9:30</span>
    <svg width="44" height="10" viewBox="0 0 44 10" fill="#fff"><rect x="0" y="6" width="2" height="4"/><rect x="3" y="4" width="2" height="6"/><rect x="6" y="2" width="2" height="8"/><rect x="9" y="0" width="2" height="10"/><path d="M16 4a7 7 0 0 1 10 0l-1 1a5.5 5.5 0 0 0-8 0z M18 6a4 4 0 0 1 6 0l-3 3z"/><rect x="30" y="1" width="12" height="8" rx="1.5" fill="none" stroke="#fff"/><rect x="31.5" y="2.5" width="9" height="5"/><rect x="42.5" y="3.5" width="1.2" height="3"/></svg>
  </div>
  <div class="brand" style="top:56px">Hiring Helper</div>
  <div class="sheet" style="top:129px"></div>
  <div class="option" style="top:192px">View Questions &amp; Responsses</div>
  <div class="option" style="top:260px">My Questions Portfolio</div>
  <div class="option" style="top:326px">Interview Tips</div>
  <div class="illustration" role="img" aria-label="Illustration of a person studying on a laptop with a video screen and chat bubbles"></div>
  <nav class="nav">
    <svg width="16" height="16" viewBox="0 0 16 16" fill="var(--nav-active)"><path d="M8 1L1 7.5h2V15h4v-4h2v4h4V7.5h2z"/></svg>
    <svg width="16" height="16" viewBox="0 0 16 16" fill="none" stroke="var(--nav-icon)" stroke-width="2"><circle cx="7" cy="7" r="5"/><path d="M11 11l4 4"/></svg>
    <svg width="18" height="18" viewBox="0 0 18 18"><rect width="18" height="18" rx="4" fill="var(--nav-icon)"/><path d="M9 5v8M5 9h8" stroke="#fff" stroke-width="2"/></svg>
    <svg width="17" height="15" viewBox="0 0 17 15" fill="var(--nav-icon)"><path d="M8.5 15L1.5 8A4 4 0 0 1 8.5 2.5 4 4 0 0 1 15.5 8z"/></svg>
    <svg width="16" height="16" viewBox="0 0 16 16" fill="var(--nav-icon)"><circle cx="8" cy="5" r="4"/><path d="M0 16c0-5 3.5-6.5 8-6.5s8 1.5 8 6.5z"/></svg>
  </nav>
</section>

<!-- Category screen -->
<section class="screen screen--categories">
  <div class="header" role="img" aria-label="Blue-tinted photo of an interview meeting"></div>
  <div class="status"><span>9:30</span>
    <svg width="44" height="10" viewBox="0 0 44 10" fill="#fff"><rect x="0" y="6" width="2" height="4"/><rect x="3" y="4" width="2" height="6"/><rect x="6" y="2" width="2" height="8"/><rect x="9" y="0" width="2" height="10"/><path d="M16 4a7 7 0 0 1 10 0l-1 1a5.5 5.5 0 0 0-8 0z M18 6a4 4 0 0 1 6 0l-3 3z"/><rect x="30" y="1" width="12" height="8" rx="1.5" fill="none" stroke="#fff"/><rect x="31.5" y="2.5" width="9" height="5"/><rect x="42.5" y="3.5" width="1.2" height="3"/></svg>
  </div>
  <div class="brand" style="top:42px">Hiring Helper</div>
  <div class="sheet" style="top:104px"></div>
  <h2 class="section-title">View Questions &amp; Responsses</h2>
  <p class="section-sub">Selection Your Question Category</p>
  <div class="option" style="top:234px">Behavioural</div>
  <div class="option" style="top:302px">Situational</div>
  <div class="option" style="top:368px">Motivational</div>
  <div class="option" style="top:434px">Technical</div>
  <div class="btn-view-all">View All</div>
  <nav class="nav">
    <svg width="16" height="16" viewBox="0 0 16 16" fill="var(--nav-active)"><path d="M8 1L1 7.5h2V15h4v-4h2v4h4V7.5h2z"/></svg>
    <svg width="16" height="16" viewBox="0 0 16 16" fill="none" stroke="var(--nav-icon)" stroke-width="2"><circle cx="7" cy="7" r="5"/><path d="M11 11l4 4"/></svg>
    <svg width="18" height="18" viewBox="0 0 18 18"><rect width="18" height="18" rx="4" fill="var(--nav-icon)"/><path d="M9 5v8M5 9h8" stroke="#fff" stroke-width="2"/></svg>
    <svg width="17" height="15" viewBox="0 0 17 15" fill="var(--nav-icon)"><path d="M8.5 15L1.5 8A4 4 0 0 1 8.5 2.5 4 4 0 0 1 15.5 8z"/></svg>
    <svg width="16" height="16" viewBox="0 0 16 16" fill="var(--nav-icon)"><circle cx="8" cy="5" r="4"/><path d="M0 16c0-5 3.5-6.5 8-6.5s8 1.5 8 6.5z"/></svg>
  </nav>
</section>

</body>
</html>
```